Satchel & Sundial needs new business card design

I need a new business card design. I'm looking for out-of-the-box design which represents the freedom of being a location independent entrepreneur.
I offer coaching, retreats and trips.
I would like to see designs with and without the photo.
Colors I use are black (#000000), green (#25A796) and brown (#D7C38C)
Website satchelandsundial.example

Target Market(s)

location independent entrepreneurs, digital nomads, people looking to swap the 9 to 5 for a lifestyle business

Industry/Entity Type

Business

Contact Information for Business Card

Dorota Falkner
Your Lifestyle Business Coach, Retreat & Trip Leader
http://satchelandsundial.example
hello@satchelandsundial.example
Live a life you don't need a holiday from

Font styles to use
Serif
Sans Serif

Requirements
Must have
• One side should contain only the logo. I would also consider having the "Live a life you don't need a holiday from" on that side too (depending on how it looks)
• Please show both sides on the designs.

```html
<!DOCTYPE html>
<html lang="en">
<head>
<meta charset="utf-8">
<title>Satchel &amp; Sundial – Business Card</title>
<link rel="stylesheet" href="https://fonts.googleapis.com/css2?family=Oswald:wght@400;500;600&display=swap">
<style>
  :root {
    --ink: #111111;
    --teal: #25a796;
    --paper: #f6f6f4;
    --backdrop: #dcdcda;
    --white: #ffffff;
  }
  * { box-sizing: border-box; margin: 0; padding: 0; }
  html, body {
    width: 1200px; height: 576px; overflow: hidden;
    background: var(--backdrop);
    font-family: "Oswald", "Arial Narrow", sans-serif;
  }
  .canvas { position: relative; width: 1200px; height: 576px; }

  .card {
    position: absolute; top: 138px;
    width: 484px; height: 294px;
    background: var(--paper);
    border-radius: 8px;
    overflow: hidden;
  }
  .card--front { left: 81px; }
  .card--back { left: 602px; }

  .wordmark {
    position: absolute;
    font-weight: 600;
    text-transform: uppercase;
    color: var(--ink);
    letter-spacing: 0.5px;
    white-space: nowrap;
  }
  .card--front .wordmark {
    left: 0; right: 0; top: 118px;
    text-align: center; font-size: 32px; line-height: 1;
  }
  .card--back .wordmark {
    right: 44px; top: 46px;
    font-size: 22px; line-height: 1;
  }

  .holder { position: absolute; left: 23px; top: 44px; }
  .holder__name {
    font-size: 20px; font-weight: 600; text-transform: uppercase;
    color: var(--ink); line-height: 1.1;
  }
  .holder__role {
    margin-top: 6px;
    font-size: 12px; font-weight: 400; color: var(--teal); line-height: 1.4;
  }

  .contact { position: absolute; left: 248px; top: 182px; list-style: none; }
  .contact__item {
    display: flex; align-items: center; gap: 6px;
    font-size: 12.5px; color: var(--ink); height: 20px;
  }
  .contact__icon { width: 11px; height: 11px; flex: none; }
  .contact__accent { color: var(--teal); }

  .social {
    position: absolute; left: 23px; top: 236px;
    display: flex; align-items: center; gap: 6px;
    font-size: 12.5px; color: var(--teal);
  }
  .social__mark { width: 10px; height: 10px; background: var(--ink); border-radius: 2px; }

  .footer-band { position: absolute; left: 0; bottom: 0; width: 484px; height: 42px; }
  .tagline {
    position: absolute; left: 244px; bottom: 14px;
    font-size: 14px; font-weight: 400; color: var(--white); white-space: nowrap;
  }
</style>
</head>
<body>
<main class="canvas">

  <section class="card card--front" aria-label="Card front">
    <div class="wordmark">Satchel &amp; Sundial</div>
  </section>

  <section class="card card--back" aria-label="Card back">
    <div class="holder">
      <h1 class="holder__name">Dorota Falkner</h1>
      <p class="holder__role">Your Lifestyle Business Coach<br>Retreat &amp; Trip Leader</p>
    </div>

    <div class="wordmark">Satchel &amp; Sundial</div>

    <ul class="contact">
      <li class="contact__item">
        <svg class="contact__icon" viewBox="0 0 12 12" aria-hidden="true">
          <rect x="0.5" y="2" width="11" height="8" fill="var(--teal)"/>
          <polyline points="0.5,2.5 6,7 11.5,2.5" fill="none" stroke="var(--paper)" stroke-width="1.2"/>
        </svg>
        hello@satchelandsundial.example
      </li>
      <li class="contact__item">
        <svg class="contact__icon" viewBox="0 0 12 12" aria-hidden="true">
          <circle cx="6" cy="6" r="5.2" fill="none" stroke="var(--teal)" stroke-width="1.2"/>
          <ellipse cx="6" cy="6" rx="2.2" ry="5.2" fill="none" stroke="var(--teal)" stroke-width="1"/>
          <line x1="0.8" y1="6" x2="11.2" y2="6" stroke="var(--teal)" stroke-width="1"/>
        </svg>
        <span>www.<span class="contact__accent">satchelandsundial</span>.example</span>
      </li>
    </ul>

    <div class="social">
      <span class="social__mark" aria-hidden="true"></span>
      <span>/satchelandsundial</span>
    </div>

    <svg class="footer-band" viewBox="0 0 484 42" aria-hidden="true">
      <rect x="0" y="22" width="200" height="20" fill="var(--teal)"/>
      <polygon points="210,0 484,0 484,42 186,42" fill="var(--ink)"/>
    </svg>
    <p class="tagline">Live a life you don’t need a holiday from</p>
  </section>

</main>
</body>
</html>
```